Firm Stationery Design

I need a design for stationery, including: Stationery First Page, Stationery Second Sheet, Envelope, Mailing Label for Flat Envelopes, and Business Cards

```html
<!DOCTYPE html>
<html lang="en">
<head>
<meta charset="UTF-8">
<title>Marlowe Law LLC – Envelope</title>
<link rel="stylesheet" href="https://fonts.googleapis.com/css2?family=Montserrat:wght@400;800&display=swap">
<style>
  :root {
    --backdrop: #3b3b3b;
    --paper: #f7f7f6;
    --ink: #111111;
    --accent: #f29a13;
    --flap-shade: #e9e9e8;
  }
  * { margin: 0; padding: 0; box-sizing: border-box; }
  html, body { width: 1200px; height: 800px; overflow: hidden; }
  body {
    background: var(--backdrop);
    font-family: "Montserrat", Arial, sans-serif;
    position: relative;
  }
  .envelope {
    position: absolute;
    width: 700px;
    height: 320px;
    background: var(--paper);
    overflow: hidden;
  }
  .envelope--front { left: 60px; top: 70px; z-index: 2; }
  .envelope--back { left: 440px; top: 420px; }

  .sender {
    position: absolute;
    left: 40px;
    top: 36px;
  }
  .brand {
    display: flex;
    align-items: center;
    gap: 8px;
    font-weight: 800;
    font-size: 22px;
    letter-spacing: 0.5px;
    color: var(--ink);
    text-transform: uppercase;
    white-space: nowrap;
  }
  .brand__square {
    width: 14px;
    height: 14px;
    background: var(--accent);
  }
  .sender__address {
    margin-top: 14px;
    font-size: 13px;
    line-height: 1.35;
    color: var(--ink);
  }
  .front-bands {
    position: absolute;
    right: 0;
    bottom: 0;
    width: 340px;
    height: 320px;
  }

  .flap {
    position: absolute;
    left: 0;
    top: 0;
    width: 700px;
    height: 170px;
  }
  .flap-brand {
    position: absolute;
    left: 0;
    top: 86px;
    width: 100%;
    justify-content: center;
  }
</style>
</head>
<body>
  <section class="envelope envelope--front" aria-label="Envelope front">
    <div class="sender">
      <div class="brand"><span class="brand__square"></span>Marlowe Law LLC</div>
      <p class="sender__address">Your address, City<br>State, Zip 1234</p>
    </div>
    <svg class="front-bands" viewBox="0 0 340 320" aria-hidden="true">
      <rect class="band band--ink" x="0" y="90" width="130" height="230" fill="var(--ink)"/>
      <rect class="band band--accent" x="170" y="90" width="80" height="230" fill="var(--accent)"/>
    </svg>
  </section>

  <section class="envelope envelope--back" aria-label="Envelope back">
    <svg class="flap" viewBox="0 0 700 170" aria-hidden="true">
      <path d="M0 0 H700 V130 Q700 150 680 150 H20 Q0 150 0 130 Z" fill="var(--flap-shade)"/>
      <path d="M0 0 H700 V126 Q700 144 682 144 H18 Q0 144 0 126 Z" fill="var(--paper)"/>
    </svg>
    <div class="brand flap-brand"><span class="brand__square"></span>Marlowe Law LLC</div>
  </section>
</body>
</html>
```